2 sided Handyman Postcard Design with coupon on the back

Company name is "Marlo QuickFix" Looking for a postcard that's also a business card. Showing Marlo QuickFix, 4817 Dunmore Hollow Rd NE, Brindle Falls, Ohio 43977, 740-318-6642, mtwelbeck@quillpost.example coupon- $25 off any job over $100, $50 off any job over $250, $75 off any job over $500, $100 off any job over $750, qualifications, experience 25 years. No job is to small. Handyman service. home repair. Free estimates. Examples, Flooring, Cabinets, Decks, Odd Jobs, Carpentry, Painting, Drywall repair, Ceramic tile, Screen repair, fence repair, Pressure wash, Hang a Picture, wood rot repair, Plumbing, Electrical, Small Jobs, Install ceiling fan, replace garbage disposal, toilet repair, install new lighting, Install safety grab bars, caulk tub or Kitchen, Hang Blinds/rods, Replace a switch/outlet, Replace/adjust doors and locksets, replace faucets/sinks/vanity tops, And much more. Have a signature look, I wear a aussie breezier hat on the job, full beard, and glasses. Am looking for a caricature of that with tools as main logo which should be shown on front and the back. One year warranty, Bonded, Insured. Cash or checks

```html
<!DOCTYPE html>
<html lang="en">
<head>
<meta charset="utf-8">
<title>Marlo QuickFix – Handyman Postcard</title>
<link rel="stylesheet" href="https://fonts.googleapis.com/css2?family=Delius&family=Schoolbell&display=swap">
<style>
  :root {
    --ink: #1c1c1c;
    --blue: #2a45a6;
    --navy: #0f2358;
    --white: #ffffff;
    --paper: #e6e2de;
    --rust: #b89c86;
    --steel: #cfcac6;
  }
  html, body {
    margin: 0;
    padding: 0;
    width: 1200px;
    height: 930px;
    overflow: hidden;
    background: var(--paper);
  }
  .postcard {
    position: relative;
    width: 1200px;
    height: 930px;
    overflow: hidden;
    font-family: "Delius", sans-serif;
    color: var(--ink);
  }
  .backdrop {
    position: absolute;
    inset: 0;
    background:
      radial-gradient(ellipse 420px 300px at 300px 180px, rgba(150,110,85,0.35), transparent 70%),
      radial-gradient(ellipse 500px 380px at 900px 600px, rgba(170,120,90,0.30), transparent 70%),
      radial-gradient(ellipse 380px 260px at 520px 620px, rgba(205,200,196,0.7), transparent 70%),
      linear-gradient(135deg, #e8e4e1 0%, #ddd3cc 45%, #e3dcd6 70%, #d8ccc3 100%);
  }
  .brand-name {
    position: absolute;
    left: 31px;
    top: 84px;
    margin: 0;
    font-size: 80px;
    font-weight: 400;
    line-height: 1;
    letter-spacing: 2px;
    color: var(--ink);
  }
  .contact {
    position: absolute;
    right: 66px;
    text-align: right;
    margin: 0;
    color: var(--ink);
  }
  .contact--address { top: 101px; font-size: 25px; line-height: 34px; }
  .contact--phone { top: 199px; font-size: 28px; }
  .contact--email { top: 269px; font-size: 21px; }
  .tagline {
    position: absolute;
    left: 43px;
    top: 260px;
    margin: 0;
    font-size: 24px;
  }
  .service-list {
    position: absolute;
    margin: 0;
    padding: 0;
    list-style: none;
    font-family: "Schoolbell", cursive;
    font-size: 24px;
    line-height: 35.9px;
    color: var(--blue);
  }
  .service-list li::before { content: "- "; }
  .service-list--general { left: 49px; top: 325px; }
  .service-list--small { left: 272px; top: 452px; }
  .credentials {
    position: absolute;
    left: 268px;
    top: 318px;
    width: 260px;
    margin: 0;
    text-align: center;
    font-size: 24px;
    line-height: 35px;
    color: var(--blue);
    font-weight: 700;
  }
  .more {
    position: absolute;
    left: 298px;
    top: 866px;
    margin: 0;
    font-size: 22px;
  }
  .burst {
    position: absolute;
    left: 538px;
    top: 217px;
    width: 350px;
    height: 290px;
    transform: rotate(-6deg);
  }
  .burst svg { display: block; }
  .burst-text {
    position: absolute;
    left: 555px;
    top: 300px;
    width: 300px;
    margin: 0;
    text-align: center;
    color: var(--white);
    font-size: 23px;
    line-height: 35px;
    transform: rotate(-7deg);
  }
  .mascot {
    position: absolute;
    left: 820px;
    top: 368px;
    width: 292px;
    height: 540px;
    border-radius: 140px 140px 40px 40px;
    background: linear-gradient(180deg, #e9e2c9 0%, #d9b79a 30%, #3e63b5 55%, #2d4aa0 80%, #b6874e 100%);
    opacity: 0.9;
  }
</style>
</head>
<body>
<main class="postcard">
  <div class="backdrop" role="img" aria-label="Faded photograph of worn wrenches and pliers in warm rust tones"></div>

  <h1 class="brand-name">Marlo QuickFix</h1>

  <p class="contact contact--address">4817 Dunmore Hollow Rd NE,<br>Brindle Falls, Ohio 43977</p>
  <p class="contact contact--phone">740-318-6642</p>
  <p class="contact contact--email">mtwelbeck@quillpost.example</p>

  <p class="tagline">25 years of experience. No job is too small.</p>

  <ul class="service-list service-list--general">
    <li>Flooring</li>
    <li>Cabinets</li>
    <li>Decks</li>
    <li>Odd Jobs</li>
    <li>Carpentry</li>
    <li>Painting</li>
    <li>Drywall Repair</li>
    <li>Ceramic Tile</li>
    <li>Screen Repair</li>
    <li>Fence Repair</li>
    <li>Pressure Wash</li>
    <li>Hanging Pictures</li>
    <li>Wood Rot Repair</li>
    <li>Plumbing</li>
    <li>Electrical</li>
  </ul>

  <p class="credentials">One year warranty<br>Bonded and Insured<br>Cash or checks</p>

  <ul class="service-list service-list--small">
    <li>Install Ceiling Fan</li>
    <li>Replace Garbage Disposal</li>
    <li>Toilet Repair</li>
    <li>Install New Lighting</li>
    <li>Install Safety Grab Bars</li>
    <li>Caulk Tub or Kitchen</li>
    <li>Hang Blinds/Rods</li>
    <li>Replace a Switch/Outlet</li>
    <li>Replace/Adjust Doors and Locksets</li>
    <li>Replace Faucets/Sinks/Vanity Tops</li>
  </ul>

  <p class="more">And much more!</p>

  <div class="burst">
    <svg width="350" height="290" viewBox="0 0 350 290" aria-hidden="true">
      <polygon fill="#0f2358" points="345,145 291,164 332,199 273,198 295,244 241,224 240,274 198,238 175,285 152,238 110,274 109,224 55,244 77,198 18,199 59,164 5,145 59,126 18,91 77,92 55,46 109,66 110,16 152,52 175,5 198,52 240,16 241,66 295,46 273,92 332,91 291,126"/>
    </svg>
  </div>
  <p class="burst-text">Handyman service.<br>Home repair.<br>Free estimates.</p>

  <div class="mascot" role="img" aria-label="Caricature of a bearded handyman in a wide-brim hat and glasses, wearing a blue work shirt and tool belt, holding a hammer"></div>
</main>
</body>
</html>
```